Modern business card design for professional copywriter

I'd like a business card design that I can use to have my cards printed out by quillprint.com as a squared corners business card (see artwork and design guidelines here: https://help.quillprint.com/hc/en-gb/sections/200570950-QUILL-Product-Templates)

The design should be clean and modern and reflect the colours, tone and branding on my website: https://tessavorrin.com.au

Target Market(s)

Professionals, B2B small business owners

Industry/Entity Type

Business

Contact Information for Business Card

Tessa Vorrin
m: 0468 905 327
e: tessa@tessavorrin.com.au
w: tessavorrin.com.au

Font styles to use
Sans Serif

Requirements
Must have
• Tagline: "Smart copywriting for clever business people"
• Brand colours: fd8000, 009984, 666666 and black
Nice to have

```html
<!DOCTYPE html>
<html lang="en">
<head>
<meta charset="utf-8">
<title>Tessa Vorrin – Copywriter Business Card</title>
<link rel="stylesheet" href="https://fonts.googleapis.com/css2?family=Open+Sans:wght@400;600;700&display=swap">
<style>
  :root {
    --brand-orange: #f5821f;
    --brand-teal: #009984;
    --brand-grey: #666666;
    --pattern-cream: #fbe6c2;
    --pattern-warm: #f3c894;
    --card-white: #ffffff;
    --backdrop: #ececec;
    --ink-white: #ffffff;
  }
  * { box-sizing: border-box; margin: 0; padding: 0; }
  html, body {
    width: 1200px;
    height: 533px;
    overflow: hidden;
  }
  body {
    background: var(--backdrop);
    font-family: "Open Sans", Arial, sans-serif;
    position: relative;
  }
  .card {
    position: absolute;
    top: 113px;
    width: 540px;
    height: 306px;
    overflow: hidden;
    box-shadow: 0 2px 6px rgba(0, 0, 0, 0.12);
  }
  .card--front { left: 60px; }
  .card--back {
    left: 600px;
    background: var(--card-white);
    border: 1px solid var(--brand-orange);
  }

  .pattern-fill {
    position: absolute;
    background: linear-gradient(135deg, var(--pattern-cream), var(--pattern-warm) 55%, var(--pattern-cream));
  }
  .card--front .pattern-fill { inset: 0; }
  .card--back .pattern-fill {
    left: 0; top: 0; right: 0;
    height: 196px;
  }

  .front-panel {
    position: absolute;
    inset: 0;
  }
  .front-panel polygon { fill: var(--brand-orange); }

  .identity {
    position: absolute;
    left: 349px;
    top: 34px;
    color: var(--ink-white);
  }
  .identity__name {
    font-size: 14px;
    font-weight: 700;
    letter-spacing: 0.4px;
    text-transform: uppercase;
  }
  .identity__role {
    margin-top: 3px;
    font-size: 7.5px;
    font-weight: 400;
    letter-spacing: 0.5px;
    text-transform: uppercase;
  }
  .identity__rule {
    margin-top: 9px;
    width: 105px;
    height: 1px;
    background: var(--brand-teal);
  }

  .contact-list {
    position: absolute;
    left: 349px;
    top: 104px;
    list-style: none;
  }
  .contact-list__item {
    display: flex;
    align-items: center;
    height: 18px;
    margin-bottom: 23px;
  }
  .contact-list__badge {
    width: 16px;
    height: 16px;
    border-radius: 50%;
    background: var(--ink-white);
    color: var(--brand-grey);
    font-size: 7.5px;
    font-weight: 700;
    display: flex;
    align-items: center;
    justify-content: center;
    margin-right: 28px;
  }
  .contact-list__value {
    font-size: 7.5px;
    font-weight: 600;
    color: var(--brand-teal);
    letter-spacing: 0.3px;
    text-transform: uppercase;
  }

  .front-wordmark {
    position: absolute;
    right: 28px;
    bottom: 26px;
    font-size: 26px;
    font-weight: 600;
    color: var(--ink-white);
    letter-spacing: -0.3px;
  }

  .back-brand {
    position: absolute;
    left: 0; right: 0;
    top: 196px;
    bottom: 0;
    display: flex;
    flex-direction: column;
    align-items: center;
    justify-content: center;
    padding-top: 4px;
  }
  .back-brand__name {
    font-size: 30px;
    font-weight: 600;
    color: var(--brand-teal);
    letter-spacing: -0.4px;
    line-height: 1.1;
  }
  .back-brand__tagline {
    margin-top: 10px;
    font-size: 7.5px;
    font-weight: 700;
    color: var(--brand-orange);
    letter-spacing: 0.3px;
    text-transform: uppercase;
  }
</style>
</head>
<body>
  <section class="card card--front">
    <div class="pattern-fill" role="img" aria-label="Repeating pattern of open books, envelopes, pen nibs and pages in orange on cream"></div>
    <svg class="front-panel" width="540" height="306" viewBox="0 0 540 306" aria-hidden="true">
      <polygon points="198,0 540,0 540,306 185,306 226,246"/>
    </svg>

    <div class="identity">
      <h1 class="identity__name">Tessa Vorrin</h1>
      <p class="identity__role">Copywriter</p>
      <div class="identity__rule"></div>
    </div>

    <ul class="contact-list">
      <li class="contact-list__item"><span class="contact-list__badge">M</span><span class="contact-list__value">0468 905 327</span></li>
      <li class="contact-list__item"><span class="contact-list__badge">E</span><span class="contact-list__value">tessa@tessavorrin.com.au</span></li>
      <li class="contact-list__item"><span class="contact-list__badge">W</span><span class="contact-list__value">tessavorrin.com.au</span></li>
    </ul>

    <p class="front-wordmark">Tessa Vorrin</p>
  </section>

  <section class="card card--back">
    <div class="pattern-fill" role="img" aria-label="Repeating pattern of open books, envelopes, pen nibs and pages in orange on cream"></div>
    <div class="back-brand">
      <p class="back-brand__name">Tessa Vorrin</p>
      <p class="back-brand__tagline">Smart copywriting for clever business people</p>
    </div>
  </section>
</body>
</html>
```